business card - Helicopter Flight Services, Flight School, etc.

We need a business card design for a new helicopter service.

We offer Helicopter Flight Services, Aerial Filming & Photography, Flight School, and Helicopter Tours. In that order.

Summit BladeAir, Inc.
Dennis Tollerby
SummitBladeair@Kestmail.com
626-418-7352

Based at the Brenwick Airport in Van Nuys, CA. The final design should communicate integrity and safety. Pictures or logos at your discretion.

Card back side - surprise me.

```html
<!DOCTYPE html>
<html lang="en">
<head>
<meta charset="utf-8">
<title>Summit BladeAir, Inc. — Business Card</title>
<link href="https://fonts.googleapis.com/css2?family=Open+Sans:wght@400;600;700;800&display=swap" rel="stylesheet">
<style>
  :root {
    --page-bg: #ecebe8;
    --blue-light: #3aa6e0;
    --blue-mid: #1e82cc;
    --blue-deep: #0a4fa0;
    --silver: #b4b6b9;
    --grey-text: #8b8d90;
    --white: #ffffff;
    --name-blue: #1d5fb0;
  }
  * { margin: 0; padding: 0; box-sizing: border-box; }
  html, body { width: 1200px; height: 913px; overflow: hidden; }
  body {
    background: var(--page-bg);
    font-family: "Open Sans", Arial, sans-serif;
    position: relative;
  }
  .card {
    position: absolute;
    width: 540px;
    height: 310px;
    border-radius: 22px;
    overflow: hidden;
    box-shadow: 0 10px 24px rgba(0,0,0,0.18);
  }
  .card-front { left: 70px; top: 140px; background: var(--white); }
  .card-back {
    left: 590px; top: 463px;
    background: linear-gradient(160deg, var(--blue-light) 0%, var(--blue-mid) 45%, var(--blue-deep) 100%);
  }
  .front-shape { position: absolute; inset: 0; }
  .company-name {
    position: absolute;
    left: 96px; top: 46px;
    color: var(--white);
    font-weight: 800;
    text-transform: uppercase;
    line-height: 1.05;
  }
  .company-name .line-main { display: block; font-size: 44px; letter-spacing: 2px; }
  .company-name .line-sub { display: block; font-size: 22px; letter-spacing: 2px; }
  .holder {
    position: absolute;
    left: 40px; top: 238px;
    width: 250px;
    text-align: right;
  }
  .holder-name { color: var(--name-blue); font-weight: 700; font-size: 21px; line-height: 1.2; }
  .holder-role { color: var(--grey-text); font-size: 13px; }
  .contact {
    position: absolute;
    left: 312px; top: 178px;
    color: var(--blue-mid);
    font-size: 13.5px;
    line-height: 1.6;
  }
  .contact-row { display: flex; align-items: center; gap: 7px; }
  .contact-row svg { width: 13px; height: 13px; flex: none; }
  .back-brand {
    position: absolute;
    left: 80px; top: 62px;
    display: flex; align-items: center; gap: 18px;
  }
  .brand-circle {
    width: 96px; height: 96px; border-radius: 50%;
    background: linear-gradient(180deg, #d9dadc, #a7a9ac);
    border: 3px solid var(--white);
  }
  .back-name {
    color: var(--white);
    font-weight: 700;
    font-size: 24px;
    text-transform: uppercase;
    letter-spacing: 1px;
  }
  .services {
    position: absolute;
    left: 80px; top: 196px;
    color: var(--white);
    font-size: 16px;
    line-height: 1.45;
  }
</style>
</head>
<body>
  <section class="card card-front" aria-label="Business card front">
    <svg class="front-shape" viewBox="0 0 540 310" preserveAspectRatio="none" aria-hidden="true">
      <defs>
        <linearGradient id="frontBlue" x1="0" y1="0" x2="0.4" y2="1">
          <stop offset="0" stop-color="#46b0e6"/>
          <stop offset="0.5" stop-color="#1e86d0"/>
          <stop offset="1" stop-color="#0d5cb0"/>
        </linearGradient>
      </defs>
      <path d="M0,0 H540 V40 Q300,200 0,210 Z" fill="url(#frontBlue)"/>
      <path d="M0,210 Q300,200 540,40" fill="none" stroke="#b4b6b9" stroke-width="5"/>
    </svg>
    <div class="company-name">
      <span class="line-main">Summit</span>
      <span class="line-sub">BladeAir, Inc.</span>
    </div>
    <div class="contact">
      <div class="contact-row">
        <svg viewBox="0 0 24 24"><path fill="#8b8d90" d="M6.6 10.8a15.1 15.1 0 0 0 6.6 6.6l2.2-2.2a1 1 0 0 1 1-.25 11.4 11.4 0 0 0 3.6.57 1 1 0 0 1 1 1V20a1 1 0 0 1-1 1A17 17 0 0 1 3 4a1 1 0 0 1 1-1h3.5a1 1 0 0 1 1 1c0 1.25.2 2.45.57 3.57a1 1 0 0 1-.25 1z"/></svg>
        <span>626-418-7352</span>
      </div>
      <div class="contact-row">
        <svg viewBox="0 0 24 24"><rect x="2" y="5" width="20" height="14" rx="1" fill="none" stroke="#8b8d90" stroke-width="2"/><path d="M2 6l10 7 10-7" fill="none" stroke="#8b8d90" stroke-width="2"/></svg>
        <span>SummitBladeair@Kestmail.com</span>
      </div>
    </div>
    <div class="holder">
      <div class="holder-name">Dennis Tollerby</div>
      <div class="holder-role">Owner</div>
    </div>
  </section>

  <section class="card card-back" aria-label="Business card back">
    <div class="back-brand">
      <div class="brand-circle"></div>
      <div class="back-name">Summit BladeAir</div>
    </div>
    <div class="services">
      Aerial Filming &amp; Photography<br>
      Flight School<br>
      Helicopter Tours (In that order)
    </div>
  </section>
</body>
</html>
```